Company web site

Looking for a full responsive(mobile friendly) wordpress implementation

Some material is in the website -- brelvanto.wordpress.com

But looking for a template more consistent with the logo design, and more future looking.

Target Market(s)

Enterprise Clients

Industry/Entity Type

It Company

Font styles to use
Sans Serif

Colors
33a6d7
0255a3
0455a3
cfdeed
85abd2
3176b5

Requirements
Must have
• about, contact information, partner page, success stories, customer testimonials. links to social presence.
• pricing information

```html
<!DOCTYPE html>
<html lang="en">
<head>
<meta charset="utf-8">
<title>Brelvanto — Bridging Connected Devices With Enterprise Solutions</title>
<link rel="stylesheet" href="https://fonts.googleapis.com/css2?family=Open+Sans:wght@300;400;600;700&family=Exo+2:wght@400;500;600;700&display=swap">
<style>
:root{
  --blue:#1f9fd8;
  --blue-dark:#0455a3;
  --ink:#3d3d3d;
  --muted:#6b6b6b;
  --light:#f2f2f2;
  --line:#d5d5d5;
  --navy:#152030;
  --navy-2:#1b2a3d;
  --white:#ffffff;
}
*{box-sizing:border-box;margin:0;padding:0}
html,body{width:1200px;height:3651px;overflow:hidden}
body{position:relative;font-family:"Open Sans",Arial,sans-serif;color:var(--ink);background:var(--white)}
.abs{position:absolute}
.brand-word{font-family:"Open Sans",Arial,sans-serif;font-weight:700;color:var(--blue);display:inline-flex;align-items:center;gap:10px}
.brand-dot{display:inline-block;border-radius:50%;background:var(--blue)}

/* top bar */
.topbar{top:0;left:0;width:1200px;height:30px;font-size:12px;color:var(--muted)}
.topbar .phone{left:80px;top:8px;display:flex;align-items:center;gap:6px}
.topbar .phone b{color:var(--ink);font-weight:600}
.social{display:flex;gap:14px}
.social span{width:12px;height:12px;border-radius:50%;background:#8a8a8a;display:block}
.topbar .social{right:80px;top:9px}

/* nav */
.nav{top:30px;left:0;width:1200px;height:98px;background:var(--white)}
.nav .logo{left:80px;top:28px;font-size:28px}
.nav ul{list-style:none;display:flex;position:absolute;left:562px;top:0;height:98px}
.nav li{height:98px;display:flex;align-items:center;justify-content:center;font-size:16px;color:#555;padding:0 19px}
.nav li.active{background:var(--blue);color:var(--white);width:95px;flex-direction:column;font-weight:600;gap:4px}

/* hero */
.hero{top:128px;left:0;width:1200px;height:476px;overflow:hidden;background:#05080d}
.hero-art{position:absolute;inset:0;background:
  radial-gradient(ellipse 180px 150px at 74% 30%,rgba(235,245,255,.85) 0%,rgba(150,195,235,.55) 45%,rgba(60,110,160,0) 100%),
  radial-gradient(ellipse 420px 260px at 62% 30%,rgba(70,130,190,.75) 0%,rgba(30,70,110,.45) 55%,rgba(10,20,35,0) 100%),
  radial-gradient(ellipse 300px 110px at 68% 86%,rgba(230,190,160,.55) 0%,rgba(120,90,80,.25) 60%,rgba(0,0,0,0) 100%),
  linear-gradient(90deg,#05080d 0%,#0a1220 30%,#15283e 60%,#1c3552 100%)}
.hero h1{position:absolute;left:80px;top:196px;font-family:"Exo 2",Arial,sans-serif;font-weight:500;font-size:32px;line-height:42px;color:var(--white)}
.hero h1 em{font-style:normal;color:var(--blue)}
.hero .dashes{position:absolute;left:80px;top:316px;display:flex;gap:24px}
.hero .dashes i{display:block;width:34px;height:4px;background:#cfcfcf}
.hero .dashes i.on{background:var(--blue)}

/* section titles */
.sec-title{width:1200px;text-align:center;font-weight:300;font-size:36px;color:#555;font-family:"Open Sans",Arial,sans-serif}
.sec-title b{color:var(--blue);font-weight:700}
.sec-title.exo{font-family:"Exo 2",Arial,sans-serif;font-weight:400}
.sec-title.exo b{font-weight:600}
.divider{left:480px;width:240px;height:20px}

/* welcome */
.welcome{top:604px;left:0;width:1200px;height:358px;background:var(--light)}
.welcome p{position:absolute;left:80px;width:1040px;top:158px;text-align:center;font-size:14.5px;line-height:26px;color:var(--muted)}
.btn{position:absolute;height:36px;border:2px solid #9a9a9a;border-radius:4px;font-size:15px;font-weight:600;display:flex;align-items:center;justify-content:center}
.welcome .btn{left:529px;top:260px;width:142px;color:#444}

/* lifecycle */
.lifecycle{top:962px;left:0;width:1200px;height:796px}
.cycle-art{position:absolute;left:362px;top:262px;width:476px;height:466px;border-radius:50%;background:radial-gradient(circle at 50% 55%,#ffffff 0%,#f3f6f9 52%,#dfe6ed 66%,#f7f9fb 80%,#ffffff 100%)}
.stage{position:absolute;font-size:13px;line-height:20px;color:#555}
.stage h3{font-size:17px;font-weight:700;color:var(--blue);margin-bottom:6px}
.stage ul{list-style:none}
.stage li::before{content:"•";margin-right:8px;color:#777}
.stage.right{text-align:right}
.center-brand{position:absolute;left:0;width:1200px;top:530px;text-align:center;font-size:42px}

/* banner */
.banner{top:1758px;left:0;width:1200px;height:222px;overflow:hidden}
.banner-art{position:absolute;inset:0;background:radial-gradient(ellipse at 60% 110%,#3a4f66 0%,#1a2636 45%,#080c14 100%)}
.banner h2{position:absolute;top:62px;width:1200px;text-align:center;color:var(--white);font-size:25px;font-weight:600}
.banner .btn{left:528px;top:118px;width:144px;border-color:var(--white);color:var(--white);font-weight:400}

/* how it works */
.how{top:1980px;left:0;width:1200px;height:462px}
.brace{position:absolute;top:167px;height:236px;width:30px}
.step{position:absolute;top:180px;font-family:"Exo 2",Arial,sans-serif}
.step .head{display:flex;align-items:baseline;gap:12px;color:var(--blue)}
.step .num{font-size:52px;font-weight:600;line-height:52px}
.step .word{font-size:26px;font-weight:600}
.step ul{list-style:none;margin:6px 0 0 38px;font-family:"Open Sans",Arial,sans-serif;font-size:14px;line-height:21px;color:#444}
.step li::before{content:"•";margin-right:8px}
.step li.more::before{content:"";margin-right:0}
.plus{position:absolute;top:230px;font-size:44px;font-weight:300;color:var(--blue)}
.product-mark{position:absolute;left:876px;top:290px;width:250px;text-align:center;font-size:24px}

/* testimonials */
.testimonials{top:2442px;left:0;width:1200px;height:540px;background:var(--light)}
.person{position:absolute;top:172px;width:330px;text-align:center}
.avatar{width:86px;height:86px;border-radius:50%;margin:0 auto;background:radial-gradient(circle at 50% 40%,#c9b4a4,#6f6a68);border:4px solid var(--white);box-shadow:0 0 0 2px var(--line)}
.avatar.lead{box-shadow:0 0 0 3px var(--blue)}
.person .name{margin-top:18px;font-size:13px;font-weight:600;color:#444}
.person .handle{font-size:12px;color:#888;margin-top:4px}
.card{position:absolute;top:338px;width:329px;height:131px;background:var(--white);border:1px solid #dcdcdc;box-shadow:0 2px 3px rgba(0,0,0,.08)}
.card.active{border:2px solid var(--blue)}
.card p{position:absolute;left:18px;top:14px;width:292px;font-size:13px;line-height:22px;color:#666;padding-left:20px;text-indent:-20px}
.card p .mark{color:#aaa;font-size:22px;font-family:Georgia,serif;margin-right:6px}
.card time{position:absolute;left:0;right:0;bottom:0;height:28px;border-top:1px solid #e3e3e3;padding:6px 18px;font-size:10.5px;color:#999}

/* partners */
.partners{top:2982px;left:0;width:1200px;height:316px}
.partner{position:absolute;top:168px;width:188px;height:80px;border:1px solid #d4d4d4;border-radius:6px;display:flex;align-items:center;justify-content:center;gap:10px;font-size:24px;font-weight:700;color:#222}
.partner .shape{width:18px;height:18px;border-radius:50%;background:#222}
.arrow{position:absolute;top:190px;width:20px;height:36px}

/* footer */
.footer{top:3298px;left:0;width:1200px;height:309px;background:linear-gradient(180deg,var(--navy-2),var(--navy))}
.fcol{position:absolute;top:54px;color:#c9d2dc;font-size:12.5px}
.fcol h4{font-size:18px;font-weight:600;color:var(--white);margin-bottom:8px}
.fcol h4 b{color:var(--blue);font-weight:600}
.fcol .rule{width:110px;height:1px;background:#3c4d61;margin-bottom:16px}
.links{list-style:none;line-height:28px}
.links li::before{content:"•";margin-right:10px;color:#8fa0b2}
.links li.current{color:var(--blue)}
.contact p{line-height:19px;margin-bottom:12px}
.contact .row{display:flex;align-items:center;gap:10px;height:32px}
.map{width:241px;height:153px;background:linear-gradient(160deg,#e3e6e8,#c8ced3)}
.foot-brand{position:absolute;left:920px;top:130px;width:220px;text-align:center;font-size:30px}
.footer .social{position:absolute;left:968px;top:188px;gap:22px}
.footer .social span{background:#c9d2dc}
.copy{top:3607px;left:0;width:1200px;height:44px;background:var(--blue);color:var(--white);font-size:12.5px;display:flex;align-items:center;justify-content:center}
.copy b{font-weight:700;margin:0 4px}
</style>
</head>
<body>

<!-- top bar -->
<div class="abs topbar">
  <div class="abs phone">
    <svg width="13" height="13" viewBox="0 0 24 24"><path d="M6.6 10.8a15 15 0 0 0 6.6 6.6l2.2-2.2c.3-.3.7-.4 1-.2 1.1.4 2.3.6 3.6.6.6 0 1 .4 1 1V20c0 .6-.4 1-1 1C10.6 21 3 13.4 3 4c0-.6.4-1 1-1h3.5c.6 0 1 .4 1 1 0 1.3.2 2.5.6 3.6.1.3 0 .7-.2 1z" fill="#1f9fd8"/></svg>
    <span>Call Us : <b>+123 555 0142</b></span>
  </div>
  <div class="abs social"><span></span><span></span><span></span><span></span></div>
</div>

<!-- navigation -->
<header class="abs nav">
  <div class="abs logo brand-word"><span class="brand-dot" style="width:22px;height:22px"></span>Brelvanto</div>
  <ul>
    <li class="active">
      <svg width="26" height="22" viewBox="0 0 26 22"><path d="M13 1 1 11h4v10h6v-6h4v6h6V11h4z" fill="#fff"/></svg>
      Home
    </li>
    <li>Platform</li>
    <li>Partners</li>
    <li>Blog</li>
    <li>About</li>
    <li>Contact</li>
  </ul>
</header>

<!-- hero -->
<section class="abs hero">
  <div class="hero-art" role="img" aria-label="Photo of an open hand holding a tablet beneath a glowing globe surrounded by floating screens of connected people"></div>
  <h1>Bridging <em>Connected Devices</em><br>With <em>Enterprise Solutions</em></h1>
  <div class="dashes"><i></i><i class="on"></i><i></i></div>
</section>

<!-- welcome -->
<section class="abs welcome">
  <h2 class="abs sec-title" style="top:62px">Welcome To <b>Brelvanto</b></h2>
  <svg class="abs divider" style="top:118px" viewBox="0 0 240 20"><line x1="0" y1="10" x2="104" y2="10" stroke="#c8c8c8"/><line x1="136" y1="10" x2="240" y2="10" stroke="#c8c8c8"/><circle cx="120" cy="10" r="7" fill="none" stroke="#b0b0b0" stroke-width="1.5"/></svg>
  <p>Brelvanto is company which provides specialized offerings in IoT domain. Based in the heart of the Silicon Valley, California. Brelvanto is built on decades of experience and knowledge. With a off-shore development center in Eastern Europe, Brelvanto is positioned to provided extensive development capabilities to our customers.</p>
  <div class="btn">Read More</div>
</section>

<!-- product lifecycle -->
<section class="abs lifecycle">
  <h2 class="abs sec-title" style="top:58px">Product <b>Lifecycle Management</b></h2>
  <svg class="abs divider" style="top:110px" viewBox="0 0 240 20"><line x1="0" y1="10" x2="104" y2="10" stroke="#c8c8c8"/><line x1="136" y1="10" x2="240" y2="10" stroke="#c8c8c8"/><circle cx="120" cy="10" r="7" fill="none" stroke="#b0b0b0" stroke-width="1.5"/></svg>

  <div class="cycle-art" role="img" aria-label="Ring diagram of seven lifecycle stages, each shown as a circular icon around the company name"></div>

  <div class="stage" style="left:400px;top:158px;width:400px;text-align:center">
    <h3>Use</h3>
    <ul><li>Customer web portal &amp; mobile apps</li><li>Notifications, social identity &amp; advanced IoT services</li></ul>
  </div>
  <div class="stage right" style="left:40px;top:340px;width:300px">
    <h3>Provision</h3>
    <ul><li>Simplify consumer experience<br>during device activation</li><li>P2P communication via Pellix</li></ul>
  </div>
  <div class="stage right" style="left:40px;top:500px;width:300px">
    <h3>Sell</h3>
    <ul><li>End user tracking in CRM</li><li>Social identity for proactive<br>marketing</li></ul>
  </div>
  <div class="stage right" style="left:40px;top:650px;width:300px">
    <h3 style="margin-bottom:2px">Manufacture</h3>
    <ul><li>Secure manufacturing<br>Process</li><li>Device traceability in ERP</li></ul>
  </div>
  <div class="stage" style="left:870px;top:344px;width:300px">
    <h3>Support</h3>
    <ul><li>In app chat, ticketing system<br>and call center integration.</li></ul>
  </div>
  <div class="stage" style="left:900px;top:500px;width:280px">
    <h3>Monetize</h3>
    <ul><li>Recurrent user billing</li><li>Additional services &amp;<br>payment options.</li></ul>
  </div>
  <div class="stage" style="left:900px;top:650px;width:280px">
    <h3 style="margin-bottom:2px">Maintain</h3>
    <ul><li>Device health check</li><li>Software and security<br>updates</li></ul>
  </div>
  <div class="center-brand"><span class="brand-word"><span class="brand-dot" style="width:30px;height:30px"></span>Brelvanto</span></div>
</section>

<!-- banner -->
<section class="abs banner">
  <div class="banner-art" role="img" aria-label="Night view of Earth from space with a glowing network grid across the horizon"></div>
  <h2>A complete package that links IoT clouds with enterprise software solutions.</h2>
  <div class="btn">Get Started</div>
</section>

<!-- how it works -->
<section class="abs how">
  <h2 class="abs sec-title exo" style="top:60px">How <b>It Works</b></h2>
  <svg class="abs divider" style="top:112px" viewBox="0 0 240 20"><line x1="0" y1="10" x2="104" y2="10" stroke="#c8c8c8"/><line x1="136" y1="10" x2="240" y2="10" stroke="#c8c8c8"/><circle cx="120" cy="10" r="7" fill="none" stroke="#b0b0b0" stroke-width="1.5"/></svg>

  <svg class="brace" style="left:80px" viewBox="0 0 30 236"><path d="M26 2C10 2 12 30 12 60V100C12 110 8 116 2 118 8 120 12 126 12 136V176C12 206 10 234 26 234" fill="none" stroke="#888" stroke-width="2"/></svg>
  <svg class="brace" style="left:826px" viewBox="0 0 30 236"><path d="M4 2C20 2 18 30 18 60V100C18 110 22 116 28 118 22 120 18 126 18 136V176C18 206 20 234 4 234" fill="none" stroke="#888" stroke-width="2"/></svg>

  <div class="step" style="left:130px">
    <div class="head"><span class="num">1</span><span class="word">Learn</span></div>
    <ul><li>Properties</li><li>Actions</li><li>Events</li></ul>
  </div>
  <div class="plus" style="left:290px">+</div>
  <div class="step" style="left:348px">
    <div class="head"><span class="num">2</span><span class="word">Connect</span></div>
    <ul><li>Vestra Link</li><li>Corvane Hub</li><li>Pellix</li><li>Tenvar</li><li>Olmora</li><li class="more">&nbsp;&nbsp;&nbsp;&nbsp;... and others</li></ul>
  </div>
  <div class="plus" style="left:534px">+</div>
  <div class="step" style="left:592px">
    <div class="head"><span class="num">3</span><span class="word">Integrate</span></div>
    <ul><li>CRM systems</li><li>Desklane</li><li>Socialpass login</li><li>Flowtrig</li><li>Billing</li><li class="more">&nbsp;&nbsp;&nbsp;&nbsp;... and many others</li></ul>
  </div>
  <div class="product-mark"><span class="brand-word"><span class="brand-dot" style="width:18px;height:18px"></span>LinkedUnit</span></div>
</section>

<!-- testimonials -->
<section class="abs testimonials">
  <h2 class="abs sec-title" style="top:62px">Clients <b>Testimonials</b></h2>
  <svg class="abs divider" style="top:114px" viewBox="0 0 240 20"><line x1="0" y1="10" x2="104" y2="10" stroke="#c8c8c8"/><line x1="136" y1="10" x2="240" y2="10" stroke="#c8c8c8"/><circle cx="120" cy="10" r="7" fill="none" stroke="#b0b0b0" stroke-width="1.5"/></svg>

  <div class="person" style="left:80px">
    <div class="avatar lead" role="img" aria-label="Portrait photo of the client"></div>
    <div class="name">Miss Mira Talvenn</div><div class="handle">@mtalvenn</div>
  </div>
  <div class="person" style="left:435px">
    <div class="avatar" role="img" aria-label="Portrait photo of the client"></div>
    <div class="name">Miss Lisa Orvanek</div><div class="handle">@lorvanek</div>
  </div>
  <div class="person" style="left:790px">
    <div class="avatar" role="img" aria-label="Portrait photo of the client"></div>
    <div class="name">Miss Dena Pruvik</div><div class="handle">@dpruvik</div>
  </div>

  <div class="card active" style="left:80px">
    <p><span class="mark">“</span>Ut wisi enim ad minim veniam, quisl mor nostrni exerci tation ullamcorper suskcipit no lobortis norl ut aliquip.</p>
    <time>4:04PM - JULY 19, 2017</time>
  </div>
  <div class="card" style="left:436px">
    <p><span class="mark">“</span>Ut wisi enim ad minim veniam, quisl mor nostrni exerci tation ullamcorper suskcipit no lobortis norl ut aliquip.</p>
    <time>4:04PM - JULY 20, 2017</time>
  </div>
  <div class="card" style="left:791px">
    <p><span class="mark">“</span>Ut wisi enim ad minim veniam, quisl mor nostrni exerci tation ullamcorper suskcipit no lobortis norl ut aliquip.</p>
    <time>4:04PM - JULY 21, 2017</time>
  </div>
</section>

<!-- partners -->
<section class="abs partners">
  <h2 class="abs sec-title" style="top:66px">Our <b>Partners</b></h2>
  <svg class="abs divider" style="top:118px" viewBox="0 0 240 20"><line x1="0" y1="10" x2="104" y2="10" stroke="#c8c8c8"/><line x1="136" y1="10" x2="240" y2="10" stroke="#c8c8c8"/><circle cx="120" cy="10" r="7" fill="none" stroke="#b0b0b0" stroke-width="1.5"/></svg>

  <svg class="arrow" style="left:34px" viewBox="0 0 20 36"><path d="M18 2 2 18l16 16" fill="none" stroke="#ccc" stroke-width="2"/></svg>
  <div class="partner" style="left:80px"><span class="shape"></span>Kestrel</div>
  <div class="partner" style="left:292px">Varnex</div>
  <div class="partner" style="left:504px"><span class="shape"></span>Marlowe</div>
  <div class="partner" style="left:716px">Orbitra</div>
  <div class="partner" style="left:928px">Quillon</div>
  <svg class="arrow" style="left:1148px" viewBox="0 0 20 36"><path d="M2 2l16 16L2 34" fill="none" stroke="#1f9fd8" stroke-width="2"/></svg>
</section>

<!-- footer -->
<footer class="abs footer">
  <div class="fcol" style="left:80px">
    <h4>Quick <b>Links</b></h4><div class="rule"></div>
    <ul class="links"><li class="current">Home</li><li>Platform</li><li>Partners</li><li>Blog</li><li>About</li><li>Contact</li></ul>
  </div>
  <div class="fcol contact" style="left:290px">
    <h4>Contact <b>Details</b></h4><div class="rule"></div>
    <p><b style="color:#fff">Brelvanto</b><br>123, Lorem ipsum dolor sit amet,<br>euismod - 123 456</p>
    <div class="row"><svg width="12" height="12" viewBox="0 0 24 24"><path d="M6.6 10.8a15 15 0 0 0 6.6 6.6l2.2-2.2c.3-.3.7-.4 1-.2 1.1.4 2.3.6 3.6.6.6 0 1 .4 1 1V20c0 .6-.4 1-1 1C10.6 21 3 13.4 3 4c0-.6.4-1 1-1h3.5c.6 0 1 .4 1 1 0 1.3.2 2.5.6 3.6.1.3 0 .7-.2 1z" fill="#1f9fd8"/></svg>123 555 0142</div>
    <div class="row"><svg width="12" height="12" viewBox="0 0 24 24"><rect x="3" y="6" width="18" height="14" rx="2" fill="#1f9fd8"/><rect x="7" y="3" width="10" height="5" fill="#1f9fd8"/></svg>123 555 0142</div>
    <div class="row"><svg width="13" height="10" viewBox="0 0 26 20"><rect x="1" y="1" width="24" height="18" rx="2" fill="none" stroke="#1f9fd8" stroke-width="2"/><path d="M1 2l12 9 12-9" fill="none" stroke="#1f9fd8" stroke-width="2"/></svg>info@brelvanto.com</div>
  </div>
  <div class="fcol" style="left:587px">
    <h4>Location <b>Map</b></h4><div class="rule"></div>
    <div class="map" role="img" aria-label="Street map showing the office location with a red pin"></div>
  </div>
  <div class="foot-brand"><span class="brand-word"><span class="brand-dot" style="width:22px;height:22px"></span>Brelvanto</span></div>
  <div class="social"><span></span><span></span><span></span><span></span></div>
</footer>
<div class="abs copy">Copyright © 2017 <b>Brelvanto</b>. All Right Reserved.</div>

</body>
</html>
```